Business Card Design Project

Business Card
We are rebranding with a new logo
Industry/Entity Type
Business
Contact Information for Business Card
Dennis Morvale +61 487215963 dennis@quorv.com.au P.O. Box 872 Fernlow QLD 4309
Requirements
Must have
- Logo

```html
<!DOCTYPE html>
<html lang="en">
<head>
<meta charset="utf-8">
<title>Quorv International – Business Card</title>
<link rel="stylesheet" href="https://fonts.googleapis.com/css2?family=Great+Vibes&family=Roboto:wght@400;700&display=swap">
<style>
  :root {
    --page-bg: #e6e4e1;
    --card-light: #eef0f0;
    --card-light-edge: #dfe3e4;
    --panel-deep: #1b6480;
    --panel-bright: #2a8fb0;
    --panel-text: #e9f1f4;
    --brand-ink: #1d6e92;
  }
  * { box-sizing: border-box; margin: 0; padding: 0; }
  html, body {
    width: 1200px;
    height: 1010px;
    overflow: hidden;
    background: var(--page-bg);
  }
  .business-card {
    position: absolute;
    left: 100px;
    top: 215px;
    width: 1000px;
    height: 580px;
    background: linear-gradient(135deg, var(--card-light), var(--card-light-edge));
    box-shadow: 0 18px 40px rgba(0,0,0,0.18);
    overflow: hidden;
  }
  .contact-panel {
    position: absolute;
    left: 0;
    top: 0;
    width: 1000px;
    height: 580px;
  }
  .holder-name {
    position: absolute;
    left: 45px;
    top: 62px;
    font-family: "Great Vibes", cursive;
    font-size: 52px;
    color: var(--panel-text);
    line-height: 1;
  }
  .holder-title {
    position: absolute;
    left: 46px;
    top: 136px;
    font-family: "Roboto", sans-serif;
    font-size: 22px;
    color: var(--panel-text);
  }
  .contact-list {
    position: absolute;
    left: 46px;
    top: 428px;
    list-style: none;
    font-family: "Roboto", sans-serif;
    font-size: 22px;
    color: var(--panel-text);
  }
  .contact-item {
    display: flex;
    align-items: center;
    height: 33px;
  }
  .contact-icon {
    width: 22px;
    height: 22px;
    margin-right: 20px;
    fill: var(--panel-text);
  }
  .brand-block {
    position: absolute;
    left: 560px;
    top: 0;
    width: 440px;
    height: 580px;
    display: flex;
    align-items: center;
    justify-content: center;
    gap: 14px;
  }
  .brand-dot {
    width: 22px;
    height: 22px;
    border-radius: 50%;
    background: var(--brand-ink);
  }
  .brand-name {
    font-family: "Roboto", sans-serif;
    font-weight: 700;
    font-size: 34px;
    letter-spacing: 1px;
    color: var(--brand-ink);
  }
</style>
</head>
<body>
  <div class="business-card">
    <svg class="contact-panel" viewBox="0 0 1000 580" aria-hidden="true">
      <defs>
        <linearGradient id="panelFill" x1="0" y1="0" x2="1" y2="1">
          <stop offset="0" stop-color="var(--panel-deep)"/>
          <stop offset="1" stop-color="var(--panel-bright)"/>
        </linearGradient>
      </defs>
      <path d="M0 0 H577 Q440 290 577 580 H0 Z" fill="url(#panelFill)"/>
    </svg>

    <div class="holder-name">Dennis Morvale</div>
    <div class="holder-title">Managing Director</div>

    <ul class="contact-list">
      <li class="contact-item">
        <svg class="contact-icon" viewBox="0 0 24 24"><path d="M6.6 10.8a15 15 0 0 0 6.6 6.6l2.2-2.2c.3-.3.7-.4 1-.2 1.1.4 2.3.6 3.6.6.6 0 1 .4 1 1V20c0 .6-.4 1-1 1A17 17 0 0 1 3 4c0-.6.4-1 1-1h3.5c.6 0 1 .4 1 1 0 1.3.2 2.5.6 3.6.1.3 0 .7-.2 1z"/></svg>
        <span>+61 487215963</span>
      </li>
      <li class="contact-item">
        <svg class="contact-icon" viewBox="0 0 24 24"><path d="M2 5h20v14H2z M3.5 6.5 12 13l8.5-6.5" fill="none" stroke="var(--panel-text)" stroke-width="2"/></svg>
        <span>dennis@quorv.com.au</span>
      </li>
      <li class="contact-item">
        <svg class="contact-icon" viewBox="0 0 24 24"><path d="M12 2a7 7 0 0 0-7 7c0 5 7 13 7 13s7-8 7-13a7 7 0 0 0-7-7zm0 9.5A2.5 2.5 0 1 1 12 6.5a2.5 2.5 0 0 1 0 5z"/></svg>
        <span>P.O. Box 872 Fernlow QLD 4309</span>
      </li>
    </ul>

    <div class="brand-block">
      <span class="brand-dot"></span>
      <span class="brand-name">Quorv International</span>
    </div>
  </div>
</body>
</html>
```